Hollow Meridian Book website design.

This is a simple one-page web design for my book.
I have all files and video needed.
Domain listed with Net Harbor.
Password and username will be given to winning bid.
Domain address, www.hollowmeridian.info
Upload a 30 second video so it can be played on the website.
Book cover photo
Book Blurb text.
Links to Rivermart and Audio books where the book can be purchased.
Below is the link to the Rivermart listing.
https://www.rivermart.example/dp/X00AAAAAA1/?coliid=QWERTYUIOPASD&colid=1ZXCVBNMLKJH0&psc=0&ref_=lv_ov_lig_dp_i
Below is the link to my Listenly books.com listing.
https://www.listenly.example/pd/Hollow-Meridian-Audiobook/X00BBBBBB2?qid=1000000001&sr=1-7&ref=a_search_c3_lProduct_1_7&pf_rd_p=00000000-aaaa-bbbb-cccc-000000000000&pf_rd_r=ZZZZ00000000000000QQ
Text on page.” Click on either logo to go directly to Rivermart or Listenly.com
Link Listenly book logo to my book on Listenly.com
Place this text under Listenly.com logo: “Free to new members of Listenly.com”
Link Rivermart logo to my book on Rivermart.
Place this text under Rivermart logo “ Free to new Pagewisp members on Rivermart.com”
Link the book photo to the Rivermart.com web address as well.
Enter meta tags or keywords below for search engines to locate webpage.
Hollow Meridian
Conspiracy
Conspiracy Books
Spy books
Thriller books
Suspense books
Comedy books
Dorian Welbeck

```html
<!DOCTYPE html>
<html lang="en">
<head>
<meta charset="utf-8">
<title>Hollow Meridian — Dorian Welbeck</title>
<meta name="keywords" content="Hollow Meridian, Conspiracy, Conspiracy Books, Spy books, Thriller books, Suspense books, Comedy books, Dorian Welbeck">
<link rel="stylesheet" href="https://fonts.googleapis.com/css2?family=Roboto+Condensed:wght@400;700&family=Lato:wght@400;700&display=swap">
<style>
:root{
  --navy:#28226b;
  --ink:#111111;
  --orange:#f7941d;
  --link:#2a1fb5;
  --footer:#07061f;
  --white:#ffffff;
  --text:#222222;
  --rule:#2c2b45;
}
*{margin:0;padding:0;box-sizing:border-box}
html,body{width:716px;height:1200px;overflow:hidden;background:var(--white)}
body{position:relative;font-family:'Lato',sans-serif;color:var(--text)}
.abs{position:absolute}
a{text-decoration:none;color:inherit}

/* header */
.top-rule{left:0;top:0;width:716px;height:3px;background:var(--navy)}
.site-header{left:0;top:3px;width:716px;height:41px;background:var(--white)}
.brand{left:68px;top:13px;font:700 15px 'Roboto Condensed',sans-serif;color:var(--ink);letter-spacing:.1px}
.nav a{position:absolute;top:17px;font:400 9px 'Roboto Condensed',sans-serif;color:var(--ink);letter-spacing:.2px}
.nav .active::after{content:"";position:absolute;left:0;right:0;top:12px;height:1.5px;background:var(--orange)}
.phone-dot{left:452px;top:13px;width:20px;height:20px;border-radius:50%;background:var(--orange)}
.phone-num{left:479px;top:18px;font:700 9px 'Roboto Condensed',sans-serif;color:var(--ink)}
.btn{display:flex;align-items:center;background:var(--navy);color:var(--white);border-radius:15px;font:700 9px 'Roboto Condensed',sans-serif}
.btn .dot{margin-left:auto;width:22px;height:22px;border-radius:50%;background:var(--white);display:flex;align-items:center;justify-content:center;margin-right:3px}
.signup{left:568px;top:8px;width:80px;height:28px;padding-left:13px}

/* hero */
.hero{left:0;top:44px;width:716px;height:360px;background:
  radial-gradient(ellipse at 60% 90%,#3d4a26 0%,transparent 55%),
  radial-gradient(ellipse at 15% 40%,#5c5a4a 0%,transparent 45%),
  linear-gradient(180deg,#4a4e78 0%,#5e6284 45%,#4b4f3a 80%,#3a3f24 100%)}
.hero-panel{left:68px;top:149px;width:278px;height:151px;background:rgba(50,52,70,.72)}
.hero-title{left:83px;color:var(--white);font-family:'Roboto Condensed',sans-serif;font-weight:700}
.hero-title.sm{top:168px;font-size:20px}
.hero-title.lg{top:202px;font-size:25px}
.get-started{left:83px;top:247px;width:97px;height:29px;padding-left:13px}
.play{left:534px;top:189px;width:68px;height:68px}
.side-social{left:672px;top:150px;width:18px;display:flex;flex-direction:column;align-items:center;gap:4px;color:var(--white);font:700 4.5px 'Roboto Condensed',sans-serif}
.side-social .ring{width:15px;height:15px;border:1px solid var(--white);border-radius:50%;display:flex;align-items:center;justify-content:center}
.side-social .line{width:1px;height:24px;background:var(--white);margin:2px 0}
.side-social .scroll{writing-mode:vertical-rl;font-size:5.5px;letter-spacing:.3px}
.side-social .knob{width:9px;height:9px;border-radius:50%;background:var(--orange)}

/* books */
.cover-3d{left:101px;top:446px;width:179px;height:263px;background:linear-gradient(135deg,#1c2a6a 0%,#6b1018 40%,#1a1a1a 75%,#000 100%);border-radius:2px 4px 4px 8px}
.cover-flat{left:412px;top:763px;width:206px;height:215px;background:linear-gradient(180deg,#000 0%,#111 38%,#3a3a3a 65%,#1a1a1a 100%)}
.sec-title{font:700 19.5px/23px 'Roboto Condensed',sans-serif;color:var(--ink)}
.blurb{font:400 8.7px/15.4px 'Lato',sans-serif;color:var(--text)}
.store-badge{display:flex;align-items:center;justify-content:center;font:700 9px 'Roboto Condensed',sans-serif}
.rivermart{left:331px;top:627px;width:49px;height:22px;background:#141414;color:var(--white)}
.listenly{left:83px;top:906px;height:20px;color:var(--ink);font-size:13px;justify-content:flex-start}
.note{font:700 8.3px 'Roboto Condensed',sans-serif;color:var(--ink)}
.go{font:700 8.3px 'Roboto Condensed',sans-serif;color:var(--link)}
.go span{color:var(--orange)}

/* footer */
.site-footer{left:0;top:1028px;width:716px;height:172px;background:var(--footer)}
.f-brand{left:66px;top:1056px;font:700 12px 'Roboto Condensed',sans-serif;color:var(--white)}
.f-head{top:1056px;font:700 8.5px 'Roboto Condensed',sans-serif;color:var(--white)}
.f-text{font:400 8.7px/15.4px 'Lato',sans-serif;color:var(--white)}
.f-link{left:276px;font:400 8.7px 'Lato',sans-serif;color:var(--white)}
.f-contact{left:392px;display:flex;align-items:center;gap:9px;font:400 8.7px 'Lato',sans-serif;color:var(--white)}
.f-contact svg{width:9px;height:9px}
.f-box{width:19px;height:19px;border:1px solid var(--white);display:flex;align-items:center;justify-content:center;font:700 4.5px 'Roboto Condensed',sans-serif;color:var(--white)}
.f-rule{left:66px;top:1165px;width:584px;height:1px;background:var(--rule)}
.copy{left:0;top:1176px;width:716px;text-align:center;font:400 8px 'Lato',sans-serif;color:var(--white)}
</style>
</head>
<body>

<div class="abs top-rule"></div>
<header class="abs site-header"></header>
<div class="abs brand">HOLLOW MERIDIAN</div>
<nav class="nav">
  <a class="active" href="#" style="left:255px">HOME</a>
  <a href="#" style="left:295px">ABOUT US</a>
  <a href="#" style="left:349px">BOOK</a>
  <a href="#" style="left:387px">CONTACT US</a>
</nav>
<div class="abs phone-dot">
  <svg viewBox="0 0 20 20" width="20" height="20"><path d="M7 6.5c.5-.6 1.3-.6 1.7 0l.8 1.2c.3.5.2 1-.2 1.4l-.4.4c.5 1 1.3 1.8 2.3 2.3l.4-.4c.4-.4 1-.5 1.4-.2l1.2.8c.6.4.6 1.2 0 1.7l-.6.6c-.6.6-1.6.7-2.6.2-2-1-3.6-2.6-4.6-4.6-.5-1-.4-2 .2-2.6z" fill="#fff"/></svg>
</div>
<div class="abs phone-num">+ 1 888 888 8888</div>
<a class="abs btn signup" href="#">SIGN UP<span class="dot"><svg width="10" height="10" viewBox="0 0 10 10"><circle cx="5" cy="5" r="5" fill="#28226b"/><path d="M2.5 5h4M5 3l2 2-2 2" stroke="#fff" stroke-width="1.1" fill="none"/></svg></span></a>

<section class="abs hero" role="img" aria-label="Photograph of a domed capitol building among trees, with a blurred stone statue in the foreground"></section>
<div class="abs hero-panel"></div>
<div class="abs hero-title sm">WELCOME TO</div>
<div class="abs hero-title lg">HOLLOW MERIDIAN</div>
<a class="abs btn get-started" href="#">GET STARTED<span class="dot"><svg width="10" height="10" viewBox="0 0 10 10"><circle cx="5" cy="5" r="5" fill="#28226b"/><path d="M2.5 5h4M5 3l2 2-2 2" stroke="#fff" stroke-width="1.1" fill="none"/></svg></span></a>
<svg class="abs play" viewBox="0 0 68 68" aria-label="Play video">
  <circle cx="34" cy="34" r="34" fill="rgba(200,200,215,.45)"/>
  <circle cx="34" cy="34" r="25" fill="#28226b"/>
  <circle cx="34" cy="34" r="15.5" fill="#fff"/>
  <path d="M30 27.5v13l10-6.5z" fill="#111"/>
</svg>
<div class="abs side-social">
  <span class="ring">Pal</span>
  <span>Pix</span>
  <span>Chp</span>
  <span>Web</span>
  <span class="line"></span>
  <span class="scroll">SCROLL DOWN</span>
  <span class="knob"></span>
</div>

<a class="abs cover-3d" href="#" role="img" aria-label="Hardcover book cover for Hollow Meridian by Dorian Welbeck, flag and capitol artwork in red, blue and black"></a>
<h2 class="abs sec-title" style="left:331px;top:460px">HOLLOW MERIDIAN<br>PAGEWISP EDITION</h2>
<p class="abs blurb" style="left:331px;top:509px;width:290px">A fictional novel based on current events surrounding the covid 19 virous. Jack Holman is a well-respected independent journalist contracted by the Harbor Daily Ledger, upon his return from reporting on the war in Syria he is tasked to investigate the covid virus out break in China.As he digs deeper, heuncovers a hideous plot by the powers that be here in America.Jack risks life and limb to uncover the conspirers behind all of this and shed light to the American people.</p>
<a class="abs store-badge rivermart" href="#">Rivermart</a>
<div class="abs note" style="left:331px;top:662px">Free to new Pagewisp members on Rivermart.com</div>
<a class="abs go" href="#" style="left:331px;top:682px">Click to go directly to <span>Rivermart.com</span></a>

<h2 class="abs sec-title" style="left:85px;top:764px">HOLLOW MERIDIAN</h2>
<p class="abs blurb" style="left:85px;top:791px;width:280px">Lorem ipsum dolor sit amet, consectetur adipiscing elit, sed do eiusmod tempor incididunt ut labore et dolore magna aliqua. Ut enim ad minim veniam, quis nostrud exercitation ullamco laboris nisi &nbsp;aliquip commodo consequat. Duis aute irure dolor in reprehenderit in voluptate velit esse cillum dolore eu fugiat nulla pariatur. Excepteur sint occaecat cupidatat non proident, sunt in culpa qui officia deserunt mollit anlaborumllamco laboris nisi &nbsp;aliquip commodo olor in reprehenderit.</p>
<a class="abs store-badge listenly" href="#">Listenly</a>
<div class="abs note" style="left:84px;top:939px">Free to new members of Listenly.com</div>
<a class="abs go" href="#" style="left:85px;top:960px">Click &nbsp;to go directly to &nbsp;<span>Listenly.com</span></a>
<div class="abs cover-flat" role="img" aria-label="Square book artwork with the author name and title in script lettering above a black and white portrait"></div>

<footer class="abs site-footer"></footer>
<div class="abs f-brand">HOLLOWMERIDIAN</div>
<p class="abs f-text" style="left:66px;top:1077px;width:150px">Lorem ipsum dolor sit &nbsp;consectetur adipiscing &nbsp;sed do eiusmod tempor incididunt eiusmod tempo.</p>
<div class="abs f-head" style="left:276px">QUICKLINKS</div>
<a class="abs f-link" href="#" style="top:1078px">Home</a>
<a class="abs f-link" href="#" style="top:1098px">About us</a>
<a class="abs f-link" href="#" style="top:1117px">Book</a>
<a class="abs f-link" href="#" style="top:1137px">Contact us</a>
<div class="abs f-head" style="left:392px">CONTACT US</div>
<div class="abs f-contact" style="top:1079px"><svg viewBox="0 0 10 10"><path d="M1.5 1.5c.4-.5 1-.5 1.3 0l.7 1c.2.4.1.8-.2 1.1l-.3.3c.4.9 1.1 1.6 2 2l.3-.3c.3-.3.7-.4 1.1-.2l1 .7c.5.3.5.9 0 1.3l-.5.5c-.5.5-1.3.5-2 .2C3.4 7.3 2.2 6.1 1.4 4.6 1 3.9 1 3.1 1.5 2.6z" fill="#fff"/></svg>+1 888-888-8888</div>
<div class="abs f-contact" style="top:1103px"><svg viewBox="0 0 10 10"><rect x="0.5" y="2" width="9" height="6.5" fill="#fff"/><path d="M.5 2l4.5 3.5L9.5 2" stroke="#07061f" stroke-width=".8" fill="none"/></svg>info@hollowmeridian.com</div>
<div class="abs f-contact" style="top:1126px"><svg viewBox="0 0 10 10"><path d="M5 .5a3.2 3.2 0 0 0-3.2 3.2C1.8 6 5 9.5 5 9.5S8.2 6 8.2 3.7A3.2 3.2 0 0 0 5 .5z" fill="#fff"/><circle cx="5" cy="3.7" r="1.2" fill="#07061f"/></svg>23, Lorem ipsum sectetur</div>
<div class="abs f-head" style="left:601px">FOLLOWS ON</div>
<a class="abs f-box" href="#" style="left:600px;top:1081px">Pal</a>
<a class="abs f-box" href="#" style="left:626px;top:1081px">Web</a>
<a class="abs f-box" href="#" style="left:600px;top:1107px">Pix</a>
<a class="abs f-box" href="#" style="left:626px;top:1107px">Chp</a>
<div class="abs f-rule"></div>
<div class="abs copy">© &nbsp;2022 Hollow Meridian &nbsp;All Right Reserved.</div>

</body>
</html>
```